Business card design needed

I would like a one sided black business card with the information provided above. Refer to my website www.brightvolleyracquets.com.au for an example of colors I have used for my site, would like to keep this consistent for my business cards also, I will upload my logo below.

I am a new small business that provides tennis customers with racquet re stringing, tennis strings and accessories.

Industry/Entity Type

Small Business

Contact Information for Business Card

Bright Volley Tennis

Owen Whitby
Managing Director

brightvolleyracquets@mailbox.example
www.brightvolleyracquets.com.au
0491 726 305

Racquet Restringing/Tennis Strings/Accessories

Requirements
Must have
• Must have my logo and card must be black

```html
<!DOCTYPE html>
<html lang="en">
<head>
<meta charset="utf-8">
<title>Bright Volley Tennis – Business Card</title>
<link rel="stylesheet" href="https://fonts.googleapis.com/css2?family=Source+Sans+3:wght@400;600&display=swap">
<style>
  :root {
    --backdrop: #e6e3df;
    --card: #000000;
    --lime: #b9d531;
    --white: #ffffff;
    --rule: #5b6fae;
    --font: "Source Sans 3", Arial, sans-serif;
  }
  * { box-sizing: border-box; margin: 0; padding: 0; }
  html, body {
    width: 1200px;
    height: 475px;
    overflow: hidden;
    background: var(--backdrop);
    font-family: var(--font);
  }
  .canvas { position: relative; width: 1200px; height: 475px; }
  .card {
    position: absolute;
    top: 81px;
    width: 547px;
    height: 312px;
    background: var(--card);
    color: var(--white);
  }
  .card--front { left: 39px; }
  .card--back { left: 602px; overflow: hidden; }

  .brand {
    position: absolute;
    display: flex;
    align-items: center;
    gap: 10px;
    color: var(--lime);
    font-weight: 600;
    text-transform: uppercase;
    letter-spacing: 0.5px;
    white-space: nowrap;
  }
  .brand__dot {
    border-radius: 50%;
    background: var(--lime);
    flex: none;
  }
  .card--front .brand { left: 42px; top: 70px; font-size: 27px; }
  .card--front .brand__dot { width: 34px; height: 34px; }
  .card--back .brand {
    left: 50%; top: 118px; transform: translateX(-50%);
    font-size: 32px;
  }
  .card--back .brand__dot { width: 40px; height: 40px; }

  .rule {
    position: absolute;
    height: 3px;
    background: var(--rule);
    top: 177px;
  }
  .rule--long { left: 0; width: 383px; }
  .rule--tab { left: 521px; width: 30px; }

  .holder {
    position: absolute;
    right: 37px;
    top: 151px;
    text-align: right;
    color: var(--lime);
  }
  .holder__name { font-size: 18px; text-transform: uppercase; line-height: 22px; }
  .holder__role { font-size: 13.5px; line-height: 18px; }

  .contacts {
    position: absolute;
    right: 38px;
    top: 219px;
    list-style: none;
  }
  .contacts li {
    display: flex;
    align-items: center;
    justify-content: flex-end;
    gap: 12px;
    height: 19.5px;
    font-size: 13.5px;
  }
  .contacts svg { width: 12px; height: 12px; flex: none; }

  .web {
    position: absolute;
    left: 0; right: 0;
    top: 259px;
    text-align: center;
    font-size: 14.5px;
    letter-spacing: 2px;
  }
</style>
</head>
<body>
<div class="canvas">
  <section class="card card--front">
    <div class="brand"><span class="brand__dot"></span>Bright Volley Tennis</div>
    <div class="rule rule--long"></div>
    <div class="rule rule--tab"></div>
    <div class="holder">
      <p class="holder__name">Owen Whitby</p>
      <p class="holder__role">Managing Director</p>
    </div>
    <ul class="contacts">
      <li>0491 726 305
        <svg viewBox="0 0 12 12" aria-hidden="true"><path d="M3 1.5 L4.6 3.8 L3.8 4.9 Q5 7.2 7.1 8.2 L8.2 7.4 L10.5 9 L9.4 10.6 Q5.5 10.4 2.4 6.4 Q1.2 4.3 1.6 2.5 Z" fill="var(--lime)"/></svg>
      </li>
      <li>brightvolleyracquets@mailbox.example
        <svg viewBox="0 0 12 12" aria-hidden="true"><rect x="1" y="3" width="10" height="7" fill="var(--lime)"/><path d="M1 3 L6 7 L11 3" stroke="var(--card)" stroke-width="1" fill="none"/></svg>
      </li>
      <li>www.brightvolleyracquets.com.au
        <svg viewBox="0 0 12 12" aria-hidden="true"><g fill="none" stroke="var(--lime)" stroke-width="1.2"><circle cx="6" cy="6" r="4.8"/><ellipse cx="6" cy="6" rx="2" ry="4.8"/><path d="M1.2 6 H10.8"/></g></svg>
      </li>
    </ul>
  </section>

  <section class="card card--back">
    <div class="brand"><span class="brand__dot"></span>Bright Volley Tennis</div>
    <p class="web">www.brightvolleyracquets.com.au</p>
  </section>
</div>
</body>
</html>
```